Tobias Ränkel and Co stationary design

Name of business:
Tobias Ränkel and Co

Can be written as:
Tobias Ränkel and Co
Tobias Ränkel & Co
tobias ränkel & co

If broken into letters:
TR&Co
tr&co

We are a Railway Safety Training Company
Our focus is on rail safety, Rail Management, Safety Management, Train Control Training, Accident Investigation.

.

Project Deadline Extended Reason: The original date was set to commence as soon as the logo contest finished. Sketch harbor started the project as soon as it was paid. Added Thursday, May 12, 2016

Target Market(s)

Professionals, CEO's and Managing Directors

Industry/Entity Type

Management Consulting

Font styles to use
Sans Serif

Requirements
Must have
• Professional, Sharp, Creative and modern
• Please note that this is for stationary concept which must include
• - business card
• - letterhead
• - envelope
• - with compliments slip
• - document cover (like book or folder cover)
• - dividers for folders....
• These must all have a common theme or style
Nice to have
• Keep if fresh
Should not have
• Please don't sent just fonts.... Must be creative

```html
<!DOCTYPE html>
<html lang="en">
<head>
<meta charset="utf-8">
<title>Tobias Ränkel &amp; Co – Stationery</title>
<link rel="stylesheet" href="https://fonts.googleapis.com/css2?family=Exo+2:ital,wght@0,400;0,700;1,400;1,700&display=swap">
<style>
:root{
  --blue:#0d4596;
  --orange:#f5a21c;
  --grey:#e4e4e4;
  --grey-dark:#d2d2d2;
  --paper:#ffffff;
  --bg:#ece6dd;
  --ink:#333;
}
*{box-sizing:border-box;margin:0;padding:0}
html,body{width:800px;height:1200px;overflow:hidden}
body{background:var(--bg);font-family:"Exo 2",sans-serif;position:relative;color:var(--ink)}
.piece{position:absolute;background:var(--paper);overflow:hidden;box-shadow:0 2px 6px rgba(0,0,0,.15)}
.piece svg.facets{position:absolute;inset:0;width:100%;height:100%}
.brand{position:absolute;display:flex;align-items:center;gap:5px;color:var(--blue);font-weight:700;white-space:nowrap}
.brand .dot{border-radius:50%;background:var(--blue);flex:none}
.contact{position:absolute;font-size:5.5px;line-height:1.4;text-align:center;color:var(--ink)}
.tagline{font-style:italic;font-weight:700}

/* letterhead */
.letterhead{left:40px;top:16px;width:338px;height:460px}
.letterhead .brand{left:28px;top:26px;font-size:10px}
.letterhead .brand .dot{width:14px;height:14px}
.letterhead .watermark{position:absolute;left:72px;top:170px;width:180px;height:150px;border-radius:50%;background:#f3f3f3}
.letterhead .contact{left:0;right:0;bottom:14px}

/* envelope */
.envelope{left:400px;top:38px;width:378px;height:164px}
.envelope .flap-name{position:absolute;top:28px;left:0;right:0;text-align:center;color:#fff;font-size:9.5px}

/* compliments slip */
.slip{left:400px;top:218px;width:378px;height:163px}
.slip .brand{left:20px;top:40px;font-size:13px}
.slip .brand .dot{width:22px;height:22px}
.slip .contact{right:80px;bottom:12px;text-align:right}

/* business cards */
.card-front{left:400px;top:397px;width:140px;height:80px}
.card-front .brand{left:10px;top:13px;font-size:7px}
.card-front .brand .dot{width:12px;height:12px}
.card-front .name-pill{position:absolute;left:86px;top:38px;background:var(--blue);color:#fff;font-size:3.6px;padding:1px 6px;border-radius:3px}
.card-front ul{position:absolute;left:86px;top:47px;list-style:none;font-size:3.2px;line-height:1.3}
.card-front li{display:flex;gap:3px;align-items:flex-start;margin-bottom:2px}
.card-front li i{width:3px;height:3px;background:var(--orange);border-radius:50%;margin-top:.5px;flex:none}
.card-back{left:400px;top:492px;width:140px;height:80px}
.card-back .tagline{position:absolute;right:10px;top:10px;color:#fff;font-size:6px}
.card-back .role{position:absolute;left:10px;bottom:11px;color:#fff;font-size:3.4px}

/* ID badge */
.badge{left:652px;top:440px;width:112px;height:150px;border-radius:8px;background:#f4f4f4;padding:7px}
.badge .face{position:relative;width:100%;height:100%;background:#fff;overflow:hidden}
.badge .brand{left:0;right:0;top:6px;justify-content:center;flex-direction:column;gap:2px;color:#fff;font-size:5px}
.badge .brand .dot{width:12px;height:12px;background:#fff}
.badge .photo{position:absolute;left:31px;top:44px;width:36px;height:40px;background:linear-gradient(#8a8f93,#d8cfc5)}
.badge .person{position:absolute;left:0;right:0;top:92px;text-align:center;font-size:5.5px;color:var(--ink)}
.badge .person small{display:block;font-size:4.4px}
.badge .foot{position:absolute;left:0;right:0;bottom:4px;text-align:center;color:#fff;font-size:3.2px}

/* pens */
.pen{position:absolute;left:84px;width:234px;height:12px;border-radius:6px 3px 3px 6px;display:flex;align-items:center;padding-left:34px;font-size:8.5px;color:#fff}
.pen::before{content:"";position:absolute;left:-4px;top:3px;width:8px;height:6px;border-radius:2px;background:#777}
.pen::after{content:"";position:absolute;right:-10px;top:4px;width:12px;height:4px;background:#999;border-radius:0 2px 2px 0}
.pen.blue{top:524px;background:var(--blue)}
.pen.orange{top:580px;background:var(--orange)}

/* folders */
.tab{position:absolute;background:var(--orange)}
.tab.front{left:22px;top:620px;width:326px;height:60px;clip-path:polygon(0 100%,100% 0,100% 100%)}
.tab.back{left:452px;top:624px;width:328px;height:60px;border-radius:20px 0 0 0}
.folder{top:664px;width:359px;height:478px}
.folder.front{left:22px;border-radius:0 34px 0 0}
.folder.back{left:420px;border-radius:34px 0 0 0}
.folder.front .brand{left:0;right:0;top:60px;flex-direction:column;gap:12px;font-size:20px;justify-content:center}
.folder.front .brand .dot{width:120px;height:104px;background:none;border:14px solid var(--blue)}
.folder.front .tagline{position:absolute;left:61px;bottom:36px;color:#fff;font-size:11.5px}
.folder.back .brand{left:26px;top:378px;color:#fff;font-size:12px}
.folder.back .brand .dot{width:46px;height:46px;background:#fff}
.folder.back .contact{left:26px;top:432px;color:#fff;text-align:left}

.title{position:absolute;left:0;right:0;top:1156px;text-align:center;font-size:28px;font-style:italic;font-weight:700;color:#fff;text-shadow:0 1px 3px rgba(0,0,0,.25)}
</style>
</head>
<body>

<!-- Letterhead -->
<section class="piece letterhead">
  <svg class="facets" viewBox="0 0 338 460" preserveAspectRatio="none" aria-hidden="true">
    <polygon points="200,0 338,0 338,60" fill="var(--grey)"/>
    <polygon points="0,80 60,140 0,190" fill="var(--grey)"/>
    <polygon points="0,140 30,120 0,360" fill="#eeeeee"/>
    <polygon points="338,300 280,370 338,430" fill="#eeeeee"/>
  </svg>
  <div class="brand"><span class="dot"></span>Tobias Ränkel &amp; Co</div>
  <div class="watermark"></div>
  <p class="contact">Tobias Ränkel &amp; Co | Lorem ipsum dolor sit amet. Lakeside, Westland<br>Phone: (xxx) xxx-xxxx | tobias.r@railmail.example</p>
</section>

<!-- Envelope -->
<section class="piece envelope">
  <svg class="facets" viewBox="0 0 378 164" preserveAspectRatio="none" aria-hidden="true">
    <polygon points="200,60 300,164 160,164" fill="#efefef"/>
    <polygon points="330,120 378,90 378,164" fill="var(--grey)"/>
    <polygon points="0,0 378,0 378,20 366,60 14,60 0,30" fill="var(--blue)"/>
  </svg>
  <p class="flap-name tagline">Tobias Ränkel &amp; Co</p>
</section>

<!-- Compliments slip -->
<section class="piece slip">
  <svg class="facets" viewBox="0 0 378 163" preserveAspectRatio="none" aria-hidden="true">
    <polygon points="300,0 378,0 378,40 250,100" fill="var(--grey)"/>
    <polygon points="60,163 110,95 170,163" fill="var(--grey)"/>
    <polygon points="0,110 40,140 0,163" fill="#efefef"/>
    <polygon points="280,163 340,100 378,163" fill="#efefef"/>
  </svg>
  <div class="brand"><span class="dot"></span>TR &amp; Co</div>
  <p class="contact">Tobias Ränkel &amp; Co | Lorem ipsum dolor sit amet. Lakeside, Westland<br>Phone: (xxx) xxx-xxxx | tobias.r@railmail.example | www.tobiasrankel.example</p>
</section>

<!-- Business card front -->
<section class="piece card-front">
  <svg class="facets" viewBox="0 0 140 80" preserveAspectRatio="none" aria-hidden="true">
    <polygon points="120,0 140,0 140,40" fill="var(--grey)"/>
    <polygon points="0,50 30,80 0,80" fill="var(--grey)"/>
  </svg>
  <div class="brand"><span class="dot"></span>TR &amp; Co</div>
  <span class="name-pill">TOBIAS RANKEL</span>
  <ul>
    <li><i></i><span>Lorem ipsum dolor sit amet<br>Lakeside, Westland</span></li>
    <li><i></i><span>tobias.r@railmail.example</span></li>
    <li><i></i><span>(xxx) xxx-xxxx</span></li>
  </ul>
</section>

<!-- Business card back -->
<section class="piece card-back">
  <svg class="facets" viewBox="0 0 140 80" preserveAspectRatio="none" aria-hidden="true">
    <rect width="140" height="80" fill="var(--blue)"/>
    <polygon points="0,0 20,0 0,30" fill="#fff"/>
    <polygon points="0,40 40,25 110,68 140,55 140,80 0,80" fill="var(--grey)"/>
    <polygon points="0,60 40,40 105,80 0,80" fill="var(--blue)"/>
  </svg>
  <p class="tagline">Tobias Ränkel &amp; Co</p>
  <p class="role">(TRAINING AND DEVELOPMENT CONSULTANT)</p>
</section>

<!-- ID badge -->
<section class="piece badge">
  <div class="face">
    <svg class="facets" viewBox="0 0 98 136" preserveAspectRatio="none" aria-hidden="true">
      <polygon points="0,0 98,0 98,40 0,52" fill="var(--blue)"/>
      <polygon points="0,100 98,70 98,136 0,136" fill="var(--orange)"/>
      <polygon points="0,124 98,112 98,136 0,136" fill="var(--blue)"/>
    </svg>
    <div class="brand"><span class="dot"></span>Tobias Ränkel &amp; Co</div>
    <div class="photo" role="img" aria-label="Portrait photo of the badge holder"></div>
    <p class="person">TOBIAS RANKEL<small>Lorem ipsum dolor sit amet</small></p>
    <p class="foot">We are a Railway Safety Training Company</p>
  </div>
</section>

<!-- Pens -->
<div class="pen blue tagline">Tobias Ränkel &amp; Co</div>
<div class="pen orange tagline">Tobias Ränkel &amp; Co</div>

<!-- Folder front -->
<div class="tab front"></div>
<section class="piece folder front">
  <svg class="facets" viewBox="0 0 359 478" preserveAspectRatio="none" aria-hidden="true">
    <polygon points="359,220 359,300 300,290" fill="var(--grey)"/>
    <polygon points="0,300 60,330 0,410" fill="var(--grey)"/>
    <polygon points="60,330 216,260 100,404" fill="#eeeeee"/>
    <polygon points="0,404 100,404 216,260 359,304 359,478 0,478" fill="var(--blue)"/>
  </svg>
  <div class="brand"><span class="dot"></span>Tobias Ränkel &amp; Co</div>
  <p class="tagline">We are a Railway Safety Training Company</p>
</section>

<!-- Folder back -->
<div class="tab back"></div>
<section class="piece folder back">
  <svg class="facets" viewBox="0 0 359 478" preserveAspectRatio="none" aria-hidden="true">
    <polygon points="0,180 40,230 0,260" fill="var(--grey)"/>
    <polygon points="60,260 140,240 90,330" fill="#eeeeee"/>
    <polygon points="300,380 359,330 359,430" fill="var(--grey)"/>
    <polygon points="0,272 60,260 260,404 359,404 359,478 0,478" fill="var(--blue)"/>
  </svg>
  <div class="brand"><span class="dot"></span>TR &amp; Co</div>
  <p class="contact">Tobias Ränkel &amp; Co | Lorem ipsum dolor sit amet. Lakeside, Westland<br>Phone: (xxx) xxx-xxxx | tobias.r@railmail.example</p>
</section>

<h1 class="title">Tobias Ränkel &amp; Co</h1>

</body>
</html>
```